Layout für Broschüre für chemiefreie Lösung, Kühlwasser aufzubereiten
Zielgruppe
FLUVITEK hat eine Technologie entwickelt, die in der Industrie eingesetzt wird um in geschlossenen und offenen Kühlkreisläufen ohne Biozide und Korrosion Inhibitoren das Kühlwasser aufzubereiten. Mit FLUVITEK haben die Unternehmen eine chemiefreie Lösungen gegen Biofouling, Korrosion und Kalk. Zielgruppe sind alle Unternehmen die etwas produzieren oder Klimaanlagen / Heizungssysteme betreiben. Es geht um zukunftsorientierte und vor allem nachhaltige Technologie ohne Einsatz von Chemie.
Aufgabenstellung
Wir suchen für die Broschüre ein neues Layout, dass geradlinig und klar strukturiert ist, vor allem modern. Die Broschüre sollte DIN A 4 - Format sein in der gewohnten Struktur Umschlagseite innen und außen und 8 - 10 Innenseiten. Im Layout sollte ein roter Faden zu erkennen sein, aber nicht jede Seite gleich aussehen. Die Anlagen sind nur beispielhaft vom bestehenden Material und sollten vom Layout keinesfalls eine Orientierung geben, denn das soll verändert werden. Die Anlagen sind für einen inhaltlichen Überblick.

```html
<!DOCTYPE html>
<html lang="de">
<head>
<meta charset="utf-8">
<title>Chemiefrei – Broschüre Innenseiten</title>
<link rel="stylesheet" href="https://fonts.googleapis.com/css2?family=Arimo:wght@400;700&display=swap">
<style>
  :root {
    --backdrop: #dcdcda;
    --paper: #f8f8f6;
    --panel: #d9d8d5;
    --panel-dark: #cfceca;
    --green: #4dba3b;
    --ink: #1d1d1d;
    --ink-soft: #555554;
    --rule: #8f8f8c;
    --label-bg: #d2d1ce;
  }
  * { margin: 0; padding: 0; box-sizing: border-box; }
  html, body {
    width: 1200px; height: 900px; overflow: hidden;
    background: var(--backdrop);
    font-family: "Arimo", Arial, sans-serif;
    color: var(--ink);
  }
  .spread {
    position: absolute; left: 80px; top: 50px;
    width: 1040px; height: 800px;
    display: flex;
  }
  .page {
    position: relative; width: 520px; height: 800px;
    background: var(--paper); overflow: hidden;
  }
  .page--left { border-right: 1px solid #e6e6e3; }

  /* left page */
  .intro {
    position: absolute; left: 40px; top: 114px; width: 122px;
    text-align: right;
  }
  .intro__title {
    font-size: 12.5px; font-weight: 700; letter-spacing: 0.2px;
    margin-bottom: 20px;
  }
  .intro__text {
    font-size: 7.6px; line-height: 13.4px; color: var(--ink-soft);
    margin-bottom: 13px;
  }
  .contents {
    position: absolute; left: 186px; top: 114px; right: 0; bottom: 0;
    background: linear-gradient(90deg, var(--panel-dark), var(--panel) 60%, #e0dfdc);
  }
  .contents__title {
    position: absolute; left: 19px; top: 24px;
    font-size: 20px; font-weight: 700; color: var(--green); letter-spacing: 0.4px;
  }
  .contents__list { list-style: none; position: absolute; left: 0; top: 79px; width: 265px; }
  .contents__item {
    display: flex; justify-content: space-between;
    height: 46px; padding-left: 51px;
    font-size: 10px; color: var(--ink-soft); letter-spacing: 0.3px;
  }

  /* right page */
  .foreword {
    position: absolute; left: 99px; top: 237px; width: 318px; height: 353px;
    border: 3px solid var(--green);
  }
  .foreword__label {
    position: absolute; left: 78px; top: -27px;
    width: 158px; height: 33px;
    background: var(--label-bg);
    border-left: 6px solid var(--paper); border-right: 6px solid var(--paper);
    box-sizing: content-box; margin-left: -6px;
    display: flex; align-items: center; justify-content: center;
    font-size: 20px; color: var(--green); letter-spacing: 2px;
  }
  .foreword__body {
    position: absolute; left: 34px; top: 74px; width: 244px;
    font-size: 12px; line-height: 12.8px;
  }
  .foreword__body p { margin-bottom: 10px; }

  /* footer */
  .folio {
    position: absolute; bottom: 18px; left: 52px; right: 40px;
    border-top: 1px solid var(--rule); padding-top: 5px;
    font-size: 7.5px; color: var(--ink-soft);
  }
  .page--right .folio { left: 40px; right: 52px; text-align: right; }
</style>
</head>
<body>
  <main class="spread">
    <section class="page page--left">
      <div class="intro">
        <h2 class="intro__title">OTASPED QUE</h2>
        <p class="intro__text">Ut, tenitatas volum que quiasimus ma ditium esendelenis eumquate pora por rehenimus, ut asit, qui ut quidelist laccae exerro aut reseqi pluptas et remo con plandae.</p>
        <p class="intro__text">Catem a dolo rite venet mo comnis mod et volorpo ratessunt que minour, quassimusam que as quatem est, id eni quam as volupta.</p>
      </div>
      <nav class="contents">
        <h2 class="contents__title">INHALT</h2>
        <ol class="contents__list">
          <li class="contents__item"><span>3</span><span>KAPITEL 1</span></li>
          <li class="contents__item"><span>4</span><span>KAPITEL 2</span></li>
          <li class="contents__item"><span>8</span><span>KAPITEL3</span></li>
        </ol>
      </nav>
      <footer class="folio">2 Chemiefrei</footer>
    </section>

    <section class="page page--right">
      <article class="foreword">
        <h2 class="foreword__label">VORWORT</h2>
        <div class="foreword__body">
          <p>Pa sus dellore stiunt, comnis alis aut ullent dolupta esequia dolupta sinullant por magnimin pellentio. Nam, nossunt quibus eumquunt es aborecea comnima gnianda ecepudaectur am fugiatu resecum in nonempo rerumqu iatatur?</p>
          <p>Nam repudam quid ma quis ab istius esequae nonem quas sa dolupta que pligend igendem dem vitiosam ex excerionsed maximpo rerciatSequi di sum quiassi tatem. Itam nis aut et vendign isciatu restistrum, sandae ipsam suntio oditenda consedist imus.</p>
          <p>Enia corisciae mos quis et molecep rorest,</p>
        </div>
      </article>
      <footer class="folio">Chemiefrei 3</footer>
    </section>
  </main>
</body>
</html>
```